Website Header Development

I am after a redesign of the Header of a website www.tlvoltaris.com.au.
This project is for the header only, and should fit in with the rest of the site
Target Market(s)
Business
Requirements
Should not have
- Over the top. Keep it simple

```html
<!DOCTYPE html>
<html lang="en">
<head>
<meta charset="utf-8">
<title>Voltaris Energy – Resource Efficiency</title>
<link rel="stylesheet" href="https://fonts.googleapis.com/css2?family=Alegreya:wght@700&family=Alegreya+Sans:wght@400;700&family=Cabin:wght@400;500;600&display=swap">
<style>
  :root {
    --page-bg: #f4f4f4;
    --white: #ffffff;
    --brand-blue: #22389a;
    --brand-blue-dark: #1b3390;
    --logo-blue: #1f3f8f;
    --logo-green: #2c8a3c;
    --nav-green: #2a8a3f;
    --nav-green-dark: #237a36;
    --nav-green-light: #33974a;
    --heading-navy: #14177d;
    --body-text: #1d1d1d;
    --image-tone: #d9dde2;
    --field-border: #bfbfbf;
  }
  * { box-sizing: border-box; margin: 0; padding: 0; }
  html, body { width: 1200px; height: 557px; overflow: hidden; background: var(--page-bg); }
  .page {
    position: absolute; left: 30px; top: 0; width: 1138px; height: 557px;
    background: var(--white); overflow: hidden;
    font-family: "Alegreya Sans", sans-serif; color: var(--body-text);
  }
  .site-header { position: absolute; left: 0; top: 0; width: 1138px; height: 125px; }
  .header-shape { position: absolute; left: 0; top: 0; }
  .brand {
    position: absolute; left: 64px; top: 40px;
    display: flex; align-items: center; gap: 12px;
    font-family: "Cabin", sans-serif; font-weight: 600; font-size: 39px;
    color: var(--logo-blue); letter-spacing: -0.5px;
  }
  .brand-mark { width: 30px; height: 30px; background: var(--logo-green); }
  .tagline {
    position: absolute; top: 28px; color: var(--white);
    font-family: "Cabin", sans-serif; font-weight: 500; font-size: 23px; line-height: 32px;
  }
  .tagline span { display: block; }
  .tagline .line-two { padding-left: 36px; }
  .tagline { left: 582px; }
  .contact { position: absolute; left: 918px; top: 20px; color: var(--white); font-family: "Cabin", sans-serif; font-size: 18px; }
  .contact-row { display: flex; align-items: center; gap: 8px; height: 27px; }
  .contact-icon {
    width: 20px; height: 20px; border: 2px solid var(--white); border-radius: 50%;
    font-size: 11px; font-weight: 600; display: flex; align-items: center; justify-content: center;
  }
  .main-nav { position: absolute; left: 0; top: 131px; width: 1138px; height: 59px; background: var(--nav-green); }
  .nav-bands { position: absolute; left: 0; top: 0; }
  .nav-item {
    position: absolute; color: var(--white); font-family: "Cabin", sans-serif; font-size: 13.5px; top: 14px;
  }
  .nav-item.is-major { font-weight: 600; font-size: 16px; top: 19px; }
  .page-title {
    position: absolute; left: 115px; top: 226px;
    font-family: "Alegreya", serif; font-weight: 700; font-size: 27px; color: var(--heading-navy); letter-spacing: 0.3px;
  }
  .intro { position: absolute; left: 69px; top: 282px; width: 240px; font-size: 16px; line-height: 28.5px; }
  .intro p { margin-bottom: 29px; }
  .feature-image {
    position: absolute; left: 327px; top: 296px; width: 399px; height: 261px;
    background: linear-gradient(120deg, #eef0f2 0%, var(--image-tone) 55%, #b9c2cc 100%);
  }
  .sidebar { position: absolute; left: 838px; top: 192px; width: 212px; }
  .search-field {
    width: 208px; height: 35px; border: 1px solid var(--field-border);
    display: flex; align-items: center; gap: 8px; padding-left: 10px;
    font-family: "Cabin", sans-serif; font-size: 15px; color: #a8a8a8;
  }
  .newsletter-title {
    margin-top: 42px; font-family: "Alegreya", serif; font-weight: 700; font-size: 23px;
    line-height: 34px; letter-spacing: 2px; color: var(--brand-blue-dark);
  }
  .newsletter-text { margin-top: 22px; font-size: 11.5px; font-weight: 700; line-height: 28.5px; }
  .newsletter-field { margin-top: 7px; width: 210px; height: 31px; border: 1px solid var(--field-border); }
  .newsletter-text.is-last { margin-top: 12px; }
</style>
</head>
<body>
<div class="page">
  <header class="site-header">
    <svg class="header-shape" width="1138" height="125" viewBox="0 0 1138 125">
      <defs>
        <linearGradient id="headerBlue" x1="0" y1="0" x2="1" y2="1">
          <stop offset="0" stop-color="#2b44a2"/>
          <stop offset="1" stop-color="#1d3590"/>
        </linearGradient>
      </defs>
      <rect x="0" y="0" width="1138" height="5" fill="url(#headerBlue)"/>
      <path d="M488 0 C560 2 560 125 650 125 L1138 125 L1138 0 Z" fill="url(#headerBlue)"/>
    </svg>
    <div class="brand"><span>voltaris energy</span><span class="brand-mark"></span></div>
    <div class="tagline"><span>Resource Efficiency</span><span class="line-two">Sustainable Solutions</span></div>
    <div class="contact">
      <div class="contact-row"><span class="contact-icon">P</span>+61 ( 02) 4000 3825</div>
      <div class="contact-row"><span class="contact-icon">E</span>info@tlvoltaris.com.au</div>
    </div>
  </header>

  <nav class="main-nav">
    <svg class="nav-bands" width="1138" height="59" viewBox="0 0 1138 59">
      <polygon points="0,0 300,0 270,59 0,59" fill="var(--nav-green)"/>
      <polygon points="300,0 1010,0 1075,59 270,59" fill="var(--nav-green-light)"/>
      <polygon points="1010,0 1138,0 1138,59 1075,59" fill="var(--nav-green-dark)"/>
    </svg>
    <span class="nav-item is-major" style="left:95px">Home</span>
    <span class="nav-item" style="left:181px">About Us</span>
    <span class="nav-item" style="left:272px">Services</span>
    <span class="nav-item" style="left:354px">Projects and Case Studies</span>
    <span class="nav-item is-major" style="left:541px">Financial Information</span>
    <span class="nav-item" style="left:741px">News</span>
    <span class="nav-item" style="left:808px">Contact</span>
  </nav>

  <h1 class="page-title">Resource Efficiency – Sustainable Solutions</h1>

  <div class="intro">
    <p>Is your business performing as well as your competitors?</p>
    <p>Are your fixed costs comparable to industry leaders?</p>
    <p>Is your business becoming less profitable with increased energy, waste and water prices?</p>
  </div>

  <div class="feature-image" role="img" aria-label="Photo of a businessman holding a puzzle piece beside the word Solution"></div>

  <aside class="sidebar">
    <div class="search-field">
      <svg width="14" height="16" viewBox="0 0 14 16"><circle cx="8" cy="6" r="4.5" fill="none" stroke="#a8a8a8" stroke-width="2"/><line x1="5" y1="9.5" x2="1" y2="15" stroke="#a8a8a8" stroke-width="2.5"/></svg>
      Search
    </div>
    <h2 class="newsletter-title">Voltaris<br>Energy<br>Newsletter</h2>
    <p class="newsletter-text">Would you like to receive our regular monthly Newsletter? Please fill in your Name:</p>
    <div class="newsletter-field"></div>
    <p class="newsletter-text is-last">Let us know your email address so we</p>
  </aside>
</div>
</body>
</html>
```